I need a SEO-friendly Wordpress website (making sure to style H1, H2, H3, etc correctly) for a Hawaii-based law firm called Meridian Crest Legal Group. Comparable websites include https://brvlaw.example/ and https://www.lomrit.example/ for design reference. The current copy on the TarnAdvocate.example website can be used.

```html
<!DOCTYPE html>
<html lang="en">
<head>
<meta charset="utf-8">
<title>Meridian Crest Legal Group – Kona Lawyers</title>
<link rel="stylesheet" href="https://fonts.googleapis.com/css2?family=Cinzel:wght@400;700&family=Roboto:wght@400;500;700&display=swap">
<style>
:root{
  --navy:#0b3547;
  --gold:#f5b400;
  --gold-dark:#e89c00;
  --slate:#7d8896;
  --light:#f4f4f4;
  --ink:#1c2a36;
  --heading:#2f4152;
  --white:#ffffff;
}
*{box-sizing:border-box;margin:0;padding:0}
html,body{width:698px;height:1200px;overflow:hidden;background:var(--white)}
body{font-family:"Roboto",Arial,sans-serif;color:var(--ink)}
.page{position:relative;width:698px;height:1200px;overflow:hidden}
.abs{position:absolute}

.site-header{left:0;top:0;width:698px;height:68px;background:var(--white)}
.brand-name{left:42px;top:16px;font-family:"Cinzel",serif;font-size:17px;color:var(--navy);letter-spacing:.4px}
.brand-tag{left:43px;top:41px;font-size:10.5px;letter-spacing:2.2px;color:var(--ink)}
.header-call{right:43px;top:24px;display:flex;align-items:center;gap:5px}
.header-call .ask{font-size:6.3px;line-height:8px;font-weight:500;color:var(--ink)}
.header-call .num{font-size:15.5px;font-weight:500;color:#7b8792;letter-spacing:.2px}

.main-nav{left:0;top:68px;width:698px;height:29px;background:var(--navy);display:flex;align-items:center;padding-left:42px;gap:19px}
.main-nav a{color:var(--white);text-decoration:none;font-size:8.3px;text-transform:uppercase}

.hero{left:0;top:97px;width:698px;height:304px;background:linear-gradient(90deg,#1b2735,#0f1a27 60%,#111c29)}
.hero-photo{left:0;top:0;width:395px;height:304px;background:linear-gradient(135deg,#8b9aa8 0%,#d9dde2 35%,#3b5a8c 60%,#1e2a3a 100%)}
.hero-title{left:416px;top:76px;width:260px;font-weight:700;font-size:20.5px;line-height:25px;color:var(--gold)}
.hero-text{left:417px;top:137px;width:232px;font-size:9.6px;line-height:13px;color:var(--white)}
.hero-text strong{font-weight:500;display:block}
.hero-text p+p{margin-top:5px}
.hero-dots{left:421px;top:244px;display:flex;gap:6px}
.hero-dots span{width:5px;height:5px;border-radius:50%;background:#1aa3dd}
.hero-dots span.on{background:var(--gold)}

.about-side{left:0;top:401px;width:245px;height:171px;background:var(--light)}
.about-heading{left:44px;top:435px;font-family:"Cinzel",serif;font-size:21.5px;line-height:25px;color:var(--heading);font-weight:400}
.about-main{left:245px;top:401px;width:453px;height:171px;background:var(--slate)}
.about-notch{left:245px;top:465px}
.about-sub{left:284px;top:430px;width:375px;font-family:"Cinzel",serif;font-size:13px;line-height:15.5px;color:var(--white);font-weight:400}
.about-copy{left:284px;top:467px;width:374px;font-size:8px;line-height:13px;color:var(--white)}
.btn-more{left:283px;top:518px;width:85px;height:24px;border-radius:12px;background:linear-gradient(var(--gold),var(--gold-dark));color:var(--white);font-family:"Cinzel",serif;font-size:8.5px;font-weight:700;display:flex;align-items:center;justify-content:center;text-decoration:none}

.practice-title{left:0;top:600px;width:698px;text-align:center;font-family:"Cinzel",serif;font-size:21.5px;color:var(--heading);font-weight:400}
.practice-card{top:644px;width:148px}
.practice-card svg{display:block}
.practice-name{margin-top:9px;text-align:center;font-family:"Cinzel",serif;font-size:13px;line-height:15px;color:#4a5866;font-weight:400}

.footer-nav{left:0;top:840px;width:698px;height:43px;background:var(--light);display:flex;justify-content:center;align-items:center;gap:21px}
.footer-nav a{color:var(--navy);text-decoration:none;font-size:9.2px;text-transform:uppercase}

.map-area{left:0;top:883px;width:698px;height:282px;background:linear-gradient(160deg,#ececec,#e2e3e4 60%,#ebebeb)}
.contact-box{left:75px;top:938px;width:227px;height:172px;border:1px solid var(--gold);background:rgba(255,255,255,.55)}
.contact-card{left:80px;top:943px;width:217px;height:162px;background:var(--white)}
.contact-heading{left:98px;top:962px;font-family:"Cinzel",serif;font-size:21.5px;color:var(--navy);font-weight:400}
.contact-list{left:97px;top:998px;list-style:none;font-size:8.4px;line-height:10.5px;color:var(--navy)}
.contact-list li{display:flex;gap:6px;margin-bottom:4px}
.contact-list li.gap{margin-top:5px}
.contact-list svg{flex:none;margin-top:1px}

.bottom-bar{left:0;top:1165px;width:698px;height:35px;background:var(--navy);color:var(--white);font-size:7px;display:flex;align-items:center;justify-content:space-between;padding:0 44px 0 45px}
</style>
</head>
<body>
<div class="page">

  <header class="site-header abs">
    <div class="brand-name abs">Meridian Crest Legal Group</div>
    <div class="brand-tag abs">Divorce and Personal Injury Lawyers</div>
    <div class="header-call abs">
      <svg width="13" height="13" viewBox="0 0 24 24" fill="none" stroke="#0b3547" stroke-width="1.6"><path d="M5 3l4 1 1 4-2 2a12 12 0 0 0 6 6l2-2 4 1 1 4-2 2C11 21 3 13 3 5z"/></svg>
      <div class="ask">DO YOU HAVE<br>A QUESTION?</div>
      <div class="num">1.808.555.0142</div>
    </div>
  </header>

  <nav class="main-nav abs">
    <a href="#">Home</a><a href="#">Practice Areas</a><a href="#">Attorneys</a><a href="#">Blog</a><a href="#">Contact Us</a>
  </nav>

  <section class="hero abs">
    <div class="hero-photo abs" role="img" aria-label="Photo of a smiling couple reviewing a tablet with their attorney"></div>
    <h1 class="hero-title abs">Kona Lawyers of MCLG - Legal kōkua with aloha.</h1>
    <div class="hero-text abs">
      <p>Over 70 years of combined practice, specializing in:<strong>Personal Injury</strong><strong>Family &amp; Divorce</strong><strong>Child Custody</strong></p>
      <p>Dedicated to making sure you receive the care and attention you need.</p>
    </div>
    <div class="hero-dots abs"><span></span><span></span><span class="on"></span><span></span></div>
  </section>

  <div class="about-side abs"></div>
  <h2 class="about-heading abs">About the<br>Kona Lawyers<br>of MCLG</h2>
  <div class="about-main abs"></div>
  <svg class="about-notch abs" width="18" height="30" viewBox="0 0 18 30"><path d="M0 0 L17 15 L0 30 Z" fill="#f4f4f4"/></svg>
  <h3 class="about-sub abs">Lawyers Serving the Big Island and Neighboring Islands</h3>
  <p class="about-copy abs">The experienced attorneys in the Meridian Crest Legal Group's Kailua Kona, Hawaii office provide clients with a wide range of litigation expertise, including legal claims involving divorce &amp; family, personal injury, toxic exposures, intellectual property, and real estate.</p>
  <a class="btn-more abs" href="#">Read More</a>

  <h2 class="practice-title abs">Areas of Practice</h2>

  <div class="practice-card abs" style="left:43px">
    <svg width="148" height="106" role="img" aria-label="Photo of parents arguing beside their upset child"><path d="M0 0H136L148 12V106H0Z" fill="#fff" stroke="#ddd"/><rect x="3" y="3" width="142" height="100" fill="#9a8f86"/><path d="M136 0V12H148Z" fill="#e8e8e8"/></svg>
    <h3 class="practice-name">Family &amp; Divorce</h3>
  </div>
  <div class="practice-card abs" style="left:198px">
    <svg width="148" height="106" role="img" aria-label="Photo of an injured man with his arm in a sling"><path d="M0 0H136L148 12V106H0Z" fill="#fff" stroke="#ddd"/><rect x="3" y="3" width="142" height="100" fill="#b9bcc0"/><path d="M136 0V12H148Z" fill="#e8e8e8"/></svg>
    <h3 class="practice-name">Personal Injury</h3>
  </div>
  <div class="practice-card abs" style="left:352px">
    <svg width="148" height="106" role="img" aria-label="Photo looking up at glass office towers"><defs><linearGradient id="sky" x1="0" y1="0" x2="1" y2="1"><stop offset="0" stop-color="#2a4a6e"/><stop offset=".5" stop-color="#8fb8e0"/><stop offset="1" stop-color="#1d3350"/></linearGradient></defs><path d="M0 0H136L148 12V106H0Z" fill="#fff" stroke="#ddd"/><rect x="3" y="3" width="142" height="100" fill="url(#sky)"/><path d="M136 0V12H148Z" fill="#e8e8e8"/></svg>
    <h3 class="practice-name">Corporate &amp;<br>Intellectual<br>Property</h3>
  </div>
  <div class="practice-card abs" style="left:507px">
    <svg width="148" height="106" role="img" aria-label="Photo of hands holding house keys and a model house"><path d="M0 0H136L148 12V106H0Z" fill="#fff" stroke="#ddd"/><rect x="3" y="3" width="142" height="100" fill="#c9d8ea"/><path d="M136 0V12H148Z" fill="#e8e8e8"/></svg>
    <h3 class="practice-name">Real Estate</h3>
  </div>

  <nav class="footer-nav abs">
    <a href="#">Home</a><a href="#">Practice Areas</a><a href="#">Attorneys</a><a href="#">Blog</a><a href="#">Contact Us</a>
  </nav>

  <div class="map-area abs" role="img" aria-label="Street map showing the office location"></div>
  <div class="contact-box abs"></div>
  <div class="contact-card abs"></div>
  <h2 class="contact-heading abs">Contact</h2>
  <ul class="contact-list abs">
    <li><svg width="7" height="9" viewBox="0 0 10 14"><path d="M5 0a5 5 0 0 0-5 5c0 4 5 9 5 9s5-5 5-9a5 5 0 0 0-5-5zm0 7a2 2 0 1 1 0-4 2 2 0 0 1 0 4z" fill="#0b3547"/></svg><span>Kona Lawyers of Meridian Crest Legal Group</span></li>
    <li class="gap"><svg width="7" height="9"></svg><span>48-210 Palana Highway, Suite 218<br>Halewai Bay, Hawaii 96799.</span></li>
    <li style="margin-top:-4px;margin-left:-2px"><svg width="9" height="9" viewBox="0 0 24 24"><path d="M5 2l4 1 1 5-2 2a13 13 0 0 0 6 6l2-2 5 1 1 4-3 3C10 22 2 14 2 5z" fill="#0b3547"/></svg><span>+1.808.555.0142</span></li>
    <li class="gap" style="margin-left:-2px"><svg width="9" height="8" viewBox="0 0 18 14"><rect width="18" height="14" rx="1" fill="#0b3547"/><path d="M1 1l8 6 8-6" fill="none" stroke="#fff" stroke-width="1.5"/></svg><span>clients@tarnadvocate.example</span></li>
  </ul>

  <footer class="bottom-bar abs">
    <span>COPYRIGHT © 2019 &nbsp;|&nbsp; MERIDIAN CREST LEGAL GROUP. ALL RIGHTS RESERVED.</span>
    <span>TERMS OF USE &nbsp;|&nbsp; PRIVACY POLICY</span>
  </footer>

</div>
</body>
</html>
```